Leafline Physicians WEBSITE
www.leaflinephysicians.example
This website will be used by medical doctors mainly in the United States and some from other parts of the world. These doctors all have lots of research and many years of experience with patients. We have a team of people writing a book and we want about 600 doctors to fill out a questionaire and write about their research for this book. They will be going to this website to learn about us, what we are doing, why it is important for them to be included in this book and then they will decide if they want to fill out the questionaires and upload their literature and their research to us. We need for them to watch a video . There will be a 4 minute video embedded for the front page and the content will be word press. You will receive this next week. Your development team will upload the video we will make. The doctors will send their info to our email address and they MUST agree to a "terms and conditions" or we will not accept their content. We will give each doctor the SAME password to use. They must fill out their name and email address in full in order for us to receive the information they send.
It needs to be simple yet modern and exciting. So yes, you can use for the places to click onto modern and fun styles. Whether it is carrots or asparagus or avocados or broccoli or beans or other vegetables that flash or outline a location move or whatever you come up with.. sure I am open to that. I just need a little more than any other website design. I want these doctors to fall in love with the professional website and of course the content and really want to be a part of this team and agree to be a part of this book they all deserve to be in. I want you to use all the photos I have uploaded. The "notebook photo" will go where the questionaire form is for them to fill out.
Modern
Soft Pale Green ... peaceful to the eyes
Soft Pale Blue peaceful to the eyes
Soft yellow, grey or magenta
top
www.brambleharborcause.example
http://mossgateplant.example/
I put brambleharborcause.example ONLY because I like the background of rich deep forest and the colors. If you think we it would look good to have fruits and vegetables as the background or border, then let me know if I should be sending you a photo or find one to use for now and get my opinion. Then the inside would be very very soft pale colors... pale lime green for example, pale magenta. Also I only referred to the website mossgateplant because I like the moderness of it and I like how the top words do NOT have boxes around them. But the letters are tooooo small. The grey is modern and interesting, but if we use grey it must be A LOT lighter and soft. I need for the doctors to be able to access the questions only with a password. We will have a link at the top that says Doctors Questionaire. They must be able to fill part of it out, save it and be able to return to the forms without losing all the data they put onto the questionaire. We need about 6 links at the top. I want the video for them to watch to be in the center or on the right side. Whatever you think looks best. The links at the top will say who we are, What we want to accomplish, What this book is about Why it is important you be a part of this well respected team ( I realize these are long, however we can shorten the phrases... maybe) and we will add a couple of more. You will see the logo. PLEASE make that BIG and at the top. ALSO, we have ANOTHER logo which is different that I will ALSO be using. I will upload the 2nd logo and the video next week. In the meantime please work only with the logo you have now. I have 2 fun logos to use for this website. PLEASE put the links that are at the top also on the bottom of the page too. When doctors click on to different pages I want to have these beautiful photos everywhere. You will see a photo with a little baby and LOTS of vegetables. Put that at the top of the page. Then a beautiful African American girl with food. Please put that also on the front page and ONE OTHER that has a doctor with food. Please put all of those on the front page and big. Thank you!! Leafline Physicians WEBSITE

```html
<!DOCTYPE html>
<html lang="en">
<head>
<meta charset="utf-8">
<title>Leafline Physicians</title>
<link href="https://fonts.googleapis.com/css2?family=Open+Sans:wght@400;600;700;800&display=swap" rel="stylesheet">
<style>
:root{
  --green:#6bb51f;
  --green-dark:#4e9410;
  --green-pale:#eef6df;
  --purple:#8e1f7a;
  --text:#333333;
  --white:#ffffff;
}
*{box-sizing:border-box;margin:0;padding:0}
html,body{width:1200px;height:919px;overflow:hidden}
body{position:relative;font-family:"Open Sans",Arial,sans-serif;color:var(--text);background:var(--white)}
.page-bg{position:absolute;inset:0;background:linear-gradient(180deg,#f7fbef 0%,#e6f2d2 40%,#eef6e2 70%,#ffffff 100%)}
.side-produce{position:absolute;top:150px;width:200px;height:600px;opacity:.55}
.side-produce.left{left:0;background:radial-gradient(ellipse at 10% 40%,#b8d98a 0%,#d7ebb9 45%,rgba(238,246,223,0) 75%)}
.side-produce.right{right:0;background:radial-gradient(ellipse at 90% 35%,#c7df97 0%,#e4f0cc 45%,rgba(238,246,223,0) 75%)}
.abs{position:absolute}
.brand{left:174px;top:36px;display:flex;align-items:center;gap:12px}
.brand-dot{width:40px;height:40px;border-radius:50%;background:var(--green)}
.brand-name{font-size:31px;font-weight:700;color:var(--green);line-height:1;white-space:nowrap}
.contact{left:640px;top:28px;width:300px;text-align:right}
.contact .phone{font-size:20px;font-weight:700;color:#444}
.contact .phone span{color:var(--purple);font-weight:600}
.contact .email{font-size:13px;color:#555;margin-top:2px}
.contact .email span{color:var(--green-dark)}
.social{left:958px;top:34px;display:flex;gap:8px}
.social i{display:block;width:30px;height:30px;border-radius:50%}
.social i:nth-child(1){background:#4fb3e8}
.social i:nth-child(2){background:#3b5a9a}
.social i:nth-child(3){background:#2d7fb8}
.social i:nth-child(4){background:#f08a24}
.main-nav{left:475px;top:106px;width:560px;display:flex;justify-content:space-between;list-style:none}
.main-nav li{font-size:9px;font-weight:700;text-transform:uppercase;color:#444;padding:11px 7px;border-right:1px solid #c9c9c9;white-space:nowrap;line-height:1.2}
.main-nav li:last-child{border-right:none}
.main-nav li.active{background:var(--green);color:var(--white);border-right:none}
.nav-rule{left:475px;top:142px;width:560px;height:1px;background:#cfdcbc}
.hero{left:174px;top:172px;width:548px;height:308px;background:var(--white);padding:6px;box-shadow:0 2px 8px rgba(0,0,0,.12)}
.hero-img{width:100%;height:100%;background:linear-gradient(180deg,#ffffff 0%,#f4efe8 45%,#9cc25a 70%,#d7592d 85%,#6b9c35 100%)}
.welcome-bar{left:752px;top:236px;width:4px;height:76px;background:var(--purple)}
.welcome-small{left:762px;top:234px;font-size:24px;color:#7a7a7a;font-weight:400;line-height:1.1}
.welcome-title{left:762px;top:264px;font-size:26px;font-weight:700;color:var(--purple);text-transform:uppercase;white-space:nowrap;line-height:1.2}
.welcome-text{left:762px;top:316px;width:280px;font-size:12.5px;line-height:1.5;color:#333}
.welcome-text p+p{margin-top:17px}
.section-title{left:174px;top:498px;font-size:16px;font-weight:700;color:#333}
.doctor-img{left:174px;top:526px;width:194px;height:182px;background:linear-gradient(160deg,#b24fa0 0%,#8e2a80 55%,#e7e3e6 100%);border:3px solid var(--white);box-shadow:0 1px 5px rgba(0,0,0,.15)}
.accomplish-text{left:385px;top:526px;width:338px;font-size:11.6px;line-height:1.42;color:#444}
.accomplish-text em{font-style:normal;color:var(--purple);font-weight:600}
.newsletter-title{left:385px;top:664px;font-size:24px;font-weight:800;color:var(--purple);letter-spacing:.3px;line-height:1.2}
.newsletter-title span{color:var(--green)}
.newsletter-sub{left:385px;top:696px;font-size:10px;color:#666}
.newsletter-form{left:385px;top:716px;width:336px;height:26px;display:flex}
.newsletter-form .field{flex:1;background:var(--white);border:1px solid #cfcfcf;font-size:10px;color:#999;padding:6px 8px}
.newsletter-form .btn{width:110px;background:var(--green);color:var(--white);font-size:10px;font-weight:700;text-transform:uppercase;display:flex;align-items:center;justify-content:center}
.video{left:774px;top:512px;width:254px;height:184px;border:3px solid var(--white);box-shadow:0 1px 6px rgba(0,0,0,.18);background:radial-gradient(circle at 40% 55%,#e0594f 0%,#6b90c9 35%,#2f5fa8 75%,#1f3f7a 100%)}
.video svg{position:absolute;left:98px;top:66px}
.video-caption{left:774px;top:716px;width:250px;font-size:12.5px;font-weight:700;color:var(--purple);text-transform:uppercase;line-height:1.4}
.footer-band{left:174px;top:760px;width:866px;height:80px;background:linear-gradient(180deg,rgba(198,228,143,.35) 0%,#a6d45e 55%,#b35aa3 100%);opacity:.85}
.footer-nav{left:174px;top:860px;display:flex;list-style:none}
.footer-nav li{font-size:10px;color:#333;padding:0 8px;border-right:1px solid #999;line-height:1}
.footer-nav li:first-child{padding-left:0}
.footer-nav li:last-child{border-right:none}
.copyright{left:174px;top:880px;font-size:9.5px;color:#888}
.copyright span{color:var(--purple)}
.footer-brand{left:878px;top:854px;display:flex;align-items:center;gap:8px}
.footer-brand i{width:22px;height:22px;border-radius:50%;background:var(--green)}
.footer-brand b{font-size:18px;font-weight:700;color:var(--green);white-space:nowrap}
</style>
</head>
<body>
<div class="page-bg"></div>
<div class="side-produce left" role="img" aria-label="Soft faded vegetables along the left edge"></div>
<div class="side-produce right" role="img" aria-label="Soft faded fruit along the right edge"></div>

<header>
  <div class="abs brand"><span class="brand-dot"></span><span class="brand-name">Leafline Physicians</span></div>
  <div class="abs contact">
    <div class="phone">Contact Us: <span>555.014.2290</span></div>
    <div class="email">Email: <span>leaflinephysicians.example</span></div>
  </div>
  <div class="abs social" aria-label="Social links"><i></i><i></i><i></i><i></i></div>
  <ul class="abs main-nav">
    <li class="active">Home</li>
    <li>Who we are</li>
    <li>What we want to accomplish</li>
    <li>What this book is about</li>
    <li>Why it is important</li>
  </ul>
  <div class="abs nav-rule"></div>
</header>

<main>
  <div class="abs hero"><div class="hero-img" role="img" aria-label="Baby sitting among many fresh vegetables"></div></div>

  <div class="abs welcome-bar"></div>
  <div class="abs welcome-small">welcome to</div>
  <h1 class="abs welcome-title">Leafline Physicians</h1>
  <div class="abs welcome-text">
    <p>This website will be used by medical doctors mainly in the United States and some from other parts of the world.</p>
    <p>These doctors all have lots of research and many years of experience with patients.</p>
  </div>

  <h2 class="abs section-title">What We Want To Accomplish</h2>
  <div class="abs doctor-img" role="img" aria-label="Doctor holding fresh vegetables"></div>
  <p class="abs accomplish-text">Sed ut perspiciatis unde omnis iste natus error sit voluptatem accusantium doloremque laudantium, totam rem aperiam, eaque ipsa quae ab illo inventore veritatis et quasi architecto beatae vitae dicta sunt explicabo. Nemo enim ipsam voluptatem quia voluptas sit aspernatur aut odit aut fugit, sed quia consequuntur magni dolores eos qui ratione voluptatem sequi nesciunt. <em>Neque porro quisquam est</em> qui dolorem ipsum quia dolor sit amet.</p>

  <div class="abs newsletter-title">NEWSLETTER <span>SIGNUP</span></div>
  <div class="abs newsletter-sub">Subscribe to our mailing list</div>
  <div class="abs newsletter-form"><div class="field">Email Address</div><div class="btn">Subscribe</div></div>

  <div class="abs video" role="img" aria-label="Video still of a heart with a pulse line">
    <svg width="52" height="46" viewBox="0 0 52 46"><rect width="52" height="46" rx="8" fill="#222" opacity=".85"/><path d="M20 13 L36 23 L20 33 Z" fill="#fff"/></svg>
  </div>
  <p class="abs video-caption">Neque porro quisquam est qui dolorem ipsum quia dolor sit amet neque.</p>

  <div class="abs footer-band" role="img" aria-label="Green and magenta decorative band with a row of vegetables"></div>
</main>

<footer>
  <ul class="abs footer-nav">
    <li>Home</li><li>Who we are</li><li>What we want to accomplish</li><li>What this book is about</li><li>Why it is important</li>
  </ul>
  <div class="abs copyright">Copyright © leaflinephysicians.example. All Rights Reserved. | <span>Privacy Policy</span></div>
  <div class="abs footer-brand"><i></i><b>Leafline Physicians</b></div>
</footer>
</body>
</html>
```